Animal Horse & Bedding Company Needs a Website Coded & Designed

We need a website for a new animal bedding and feed company that is visually grabbing and vibrant. We would like to see a website that displays trust, quality and confidence. Needs to be responsive and mobile friendly for all browsers and coded for both Android & IOS. SEO is also important.

Joomla or Wordpress – must be both desktop and mobile friendly with fast page load speed. Need the ability to edit ourselves in Wordpress or Joomla.

Full details attached below with some layout and content ideas.

Coding

Coded - Design and coding required

Number of Pages Required

5+ page

Font styles to use
Sans Serif

Requirements
Must have
• Needs to be responsive and mobile friendly for all browsers and coded for both Android & IOS. SEO is also important.

Wordpress – must be both desktop and mobile friendly with fast page load speed. Need the ability to edit ourselves in Wordpress.

Logo Colours:
Dark Brown
CMYK: 50 / 70 / 80 / 70
Pantone: 4625C

Orange
CMYK: 0 / 50 / 100 / 0
Pantone: 144C
Nice to have
• Use picture of building attached and super impose logo on building.

```html
<!DOCTYPE html>
<html lang="en">
<head>
<meta charset="utf-8">
<title>Harvest Haven – Bedding & Feed</title>
<link href="https://fonts.googleapis.com/css2?family=Poppins:wght@400;500;600;700&display=swap" rel="stylesheet">
<style>
:root{
  --brown:#3b1712;
  --brown-2:#4a2118;
  --orange:#f7941d;
  --orange-2:#e07b22;
  --ink:#222;
  --muted:#555;
  --white:#fff;
}
*{margin:0;padding:0;box-sizing:border-box}
html,body{width:1200px;height:3158px;overflow:hidden;background:#fff;font-family:'Poppins',sans-serif;color:var(--ink)}
.page{position:absolute;left:239px;top:76px;width:760px;height:2967px;background:#fff;box-shadow:0 4px 18px rgba(0,0,0,.18);overflow:hidden}
.abs{position:absolute}
.btn{position:absolute;background:var(--orange);color:#fff;font-size:8px;font-weight:500;text-transform:uppercase;display:flex;align-items:center;justify-content:center;letter-spacing:.3px}
/* header */
.header{left:0;top:0;width:760px;height:47px;background:#fff}
.brand{left:0;top:0;width:156px;height:42px;background:var(--brown);display:flex;align-items:center;justify-content:center;gap:7px;color:#fff;font-size:12px;font-weight:600;letter-spacing:.5px}
.brand .dot{width:12px;height:12px;border-radius:50%;background:var(--orange)}
.nav{left:185px;top:18px;display:flex;gap:28px;font-size:8px;color:#333}
.nav .on{color:var(--orange-2);border-bottom:1px solid var(--orange-2)}
.socials{left:536px;top:16px;display:flex;gap:6px}
.socials span{width:12px;height:12px;border-radius:50%;border:1px solid #ccc}
.call{left:628px;top:0;width:132px;height:47px;background:var(--orange);color:#fff;font-size:9px;font-weight:700;text-align:center;padding-top:9px;line-height:17px}
/* hero */
.hero{left:0;top:47px}
.hero-title{left:0;top:110px;width:760px;text-align:center;color:#fff;font-size:33px;font-weight:700;line-height:36px}
.hero-title em{font-style:normal;color:var(--orange)}
.hero-sub{left:0;top:197px;width:760px;text-align:center;color:#fff;font-size:20px;font-weight:500;padding-left:20px}
.dots{left:698px;top:172px;display:flex;flex-direction:column;gap:9px}
.dots span{width:7px;height:7px;border-radius:50%;background:var(--orange)}
h2{font-weight:700;color:var(--ink)}
.para{font-size:8px;line-height:14px;color:var(--muted)}
.light{color:#eee}
.bullets{list-style:none;font-size:8px;line-height:18px;color:#333}
.bullets li::before{content:"";display:inline-block;width:5px;height:5px;border-radius:50%;background:var(--orange-2);margin-right:10px;vertical-align:middle}
.rule{height:2px;background:var(--orange)}
.feature{width:180px;text-align:center;font-size:8px;line-height:13px;color:#444}
.feature h4{font-size:9px;font-weight:500;margin-bottom:22px;color:#222}
.card{width:182px;height:139px;background:#fff;text-align:center;padding-top:10px}
.stars{color:var(--orange-2);font-size:13px;letter-spacing:2px}
.card p{font-size:7px;line-height:10px;color:#444;padding:4px 22px 0}
.card .av{width:14px;height:14px;border-radius:50%;background:#d9c4b5;margin:6px auto 4px}
.card b{display:block;font-size:6px;font-weight:600}
.card small{display:block;font-size:5px;color:var(--orange-2)}
.footer{left:0;top:2731px;width:760px;height:236px;background:var(--brown);color:#fff}
.fcol h5{font-size:12px;font-weight:500;margin-bottom:12px}
.fcol ul{list-style:none;font-size:8px;line-height:18px}
.fcol li::before{content:"";display:inline-block;width:4px;height:4px;border-radius:50%;background:var(--orange);margin-right:14px;vertical-align:middle}
</style>
</head>
<body>
<div class="page">

  <!-- header -->
  <div class="abs header">
    <div class="abs brand"><span class="dot"></span>HARVEST HAVEN</div>
    <nav class="abs nav"><span class="on">Home</span><span>About</span><span>Feed</span><span>Beeding</span><span>Contact Us</span><span>Request Quote</span></nav>
    <div class="abs socials"><span></span><span></span><span></span><span></span></div>
    <div class="abs call">CALL US TODAY !<br>555-0142-778</div>
  </div>

  <!-- hero -->
  <svg class="abs hero" width="760" height="398" viewBox="0 0 760 398" role="img" aria-label="Aerial photo of red barns and farm buildings under a dark brown overlay">
    <defs><linearGradient id="hg" x1="0" y1="0" x2="0" y2="1"><stop offset="0" stop-color="#5a2a22"/><stop offset=".5" stop-color="#6e2f25"/><stop offset="1" stop-color="#4a2219"/></linearGradient></defs>
    <polygon points="0,0 760,0 760,348 380,398 0,348" fill="url(#hg)"/>
  </svg>
  <div class="abs hero-title">Welcome To <em>Animals Bedding</em><br>Company</div>
  <div class="abs hero-sub">HAPPY PAWS MAKE LIFE BETTER!</div>
  <div class="btn" style="left:318px;top:291px;width:125px;height:29px;font-size:9px">Contact us</div>
  <div class="abs dots"><span></span><span></span><span></span><span></span></div>

  <!-- about -->
  <div class="abs" style="left:100px;top:520px;width:160px;height:212px;display:flex;align-items:center;justify-content:center">
    <span style="width:22px;height:22px;border-radius:50%;background:var(--orange);margin-right:8px"></span>
    <span style="font-size:17px;font-weight:700;color:var(--brown)">HARVEST HAVEN</span>
  </div>
  <h2 class="abs" style="left:359px;top:537px;font-size:17px">About us</h2>
  <div class="abs rule" style="left:359px;top:560px;width:86px"></div>
  <div class="abs para" style="left:354px;top:573px;width:320px">
    <p>Harvest Haven is a locally owned company located in Millbrook, AB. We are dedicated in providing high quality products and services.</p>
    <p style="margin-top:4px">Producing, buying and marketing hay and straw for x amount of years. Insert blurb on ownership/history of key staff/owners.</p>
    <p style="margin-top:4px">Harvest Haven offers supply and delivery of fresh bedding as well as removal of waste bedding. Let us deliver you a container of fresh straw and haul your waste bedding away. A full service solution that is sustainable and responsible.</p>
  </div>
  <div class="btn" style="left:354px;top:702px;width:89px;height:20px">View more</div>

  <!-- kind bedding band -->
  <svg class="abs" style="left:0;top:796px" width="760" height="328" viewBox="0 0 760 328"><polygon points="0,0 760,0 760,291 402,291 379,328 356,291 0,291" fill="var(--brown)"/></svg>
  <h2 class="abs" style="left:48px;top:830px;font-size:18px;line-height:20px;color:#fff">The bedding that’s kind to<br>your animals</h2>
  <div class="abs rule" style="left:48px;top:884px;width:56px;height:1px"></div>
  <div class="abs para light" style="left:48px;top:894px;width:300px">Your animal deserves the very best in health and comfort to keep them healthy, strong and happy. Our products are designed for horses, livestock (goats, cattle and sheep), small caged animals (rabbits, guinea pigs and more).Your animal deserves the very best in health and comfort to keep them healthy, strong and happy. Our products are designed for horses, livestock (goats, cattle and sheep), small caged animals (rabbits, guinea pigs and more).<p style="margin-top:6px">QUALITY GUARANTEED Grown for quality - 100% natural with no chemicals or additives</p></div>
  <div class="abs" role="img" aria-label="Photo of a rabbit in grass" style="left:442px;top:836px;width:124px;height:103px;background:linear-gradient(135deg,#6f7a3a,#8d7a4c)"></div>
  <div class="abs" role="img" aria-label="Photo of piglets sleeping on straw" style="left:576px;top:836px;width:124px;height:103px;background:linear-gradient(135deg,#d9a78f,#b88a5a)"></div>
  <div class="abs" role="img" aria-label="Photo of a cat eating from a bowl" style="left:442px;top:948px;width:124px;height:103px;background:linear-gradient(135deg,#3a3a3a,#7b7670)"></div>
  <div class="abs" role="img" aria-label="Photo of a lamb lying on straw" style="left:576px;top:948px;width:124px;height:103px;background:linear-gradient(135deg,#e9dcc4,#c4a868)"></div>

  <!-- feeding benefits -->
  <div class="abs" role="img" aria-label="Photo of a white horse running in an autumn paddock" style="left:59px;top:1185px;width:321px;height:211px;background:linear-gradient(135deg,#7a3c1f,#b8622e 50%,#5a3222)"></div>
  <h2 class="abs" style="left:443px;top:1184px;font-size:17px">FEEDING BENEFITS</h2>
  <div class="abs rule" style="left:443px;top:1207px;width:96px;height:1px"></div>
  <ul class="abs bullets" style="left:443px;top:1224px">
    <li>100% Natural Chopped Straw</li><li>Low Dust</li><li>Chemical &amp; Additive Free</li><li>Clean &amp; Highly Absorbent</li><li>Cheaper than Wood Shavings</li><li>Economic – less used and less wasted</li><li>Environmentally Friendly – Recyclable &amp; Compostable</li>
  </ul>
  <div class="btn" style="left:459px;top:1366px;width:89px;height:20px">View more</div>

  <!-- bedding benefits -->
  <svg class="abs" style="left:0;top:1467px" width="760" height="377" viewBox="0 0 760 377" role="img" aria-label="Photo of a wild rabbit in a green and yellow meadow">
    <defs><linearGradient id="bg" x1="0" y1="0" x2="1" y2="0"><stop offset="0" stop-color="#4a2a12"/><stop offset=".45" stop-color="#7a5a1a"/><stop offset="1" stop-color="#3e2a14"/></linearGradient></defs>
    <polygon points="0,0 760,0 760,321 424,321 380,377 336,321 0,321" fill="url(#bg)"/>
  </svg>
  <h2 class="abs" style="left:121px;top:1510px;font-size:17px;color:#fff">BEDDING BENEFITS</h2>
  <div class="abs rule" style="left:121px;top:1545px;width:126px;height:1px;background:#fff"></div>
  <ul class="abs bullets" style="left:121px;top:1567px;color:#fff;line-height:16.5px">
    <li>100% Natural</li><li>Chemical &amp; Additive Free</li><li>Available in Pellets or Cubes</li><li>High Protein Content</li><li>Eliminate Waste In Feeding</li><li>Clean - Eliminates Dust From Feeding Baled Hay</li><li>Cost Effective</li><li>Convenient</li><li>Less wasted feed</li>
  </ul>
  <div class="btn" style="left:137px;top:1726px;width:87px;height:20px">View more</div>

  <!-- bulk -->
  <h2 class="abs" style="left:0;top:1882px;width:740px;text-align:center;font-size:18px">Bulk pricing and delivery</h2>
  <div class="abs rule" style="left:273px;top:1914px;width:191px;height:1px"></div>
  <div class="abs feature" style="left:49px;top:1948px"><h4>ONLINE SHOP</h4>
    <svg width="54" height="48" viewBox="0 0 54 48" fill="none" stroke="#f7941d" stroke-width="2"><rect x="2" y="2" width="50" height="34" rx="2"/><path d="M20 44h14M27 36v8M17 12h4l3 12h12l3-9H22"/><circle cx="25" cy="28" r="1.5"/><circle cx="34" cy="28" r="1.5"/></svg>
    <p style="margin-top:16px">Offering a variety of animal feeds through our online shop. If you would like us to add something to our online shop, please contact us.</p></div>
  <div class="abs feature" style="left:290px;top:1951px"><h4>DELIVERIES</h4>
    <svg width="54" height="50" viewBox="0 0 54 50" fill="none" stroke="#f7941d" stroke-width="2"><rect x="14" y="2" width="36" height="34"/><path d="M28 2v12l4-3 4 3V2M2 30l10-6 12 6h10a3 3 0 010 6H22M2 44l8-4 14 6 20-10"/></svg>
    <p style="margin-top:14px">For a small fee we can deliver your pet feed order. Just place your order online or on the website and we will call with a delivery time and date</p></div>
  <div class="abs feature" style="left:534px;top:1951px"><h4>FEED ADVICE</h4>
    <svg width="52" height="52" viewBox="0 0 52 52" fill="none" stroke="#f7941d" stroke-width="2"><rect x="2" y="2" width="48" height="48" rx="12"/><path d="M36 10h8v8"/><circle cx="26" cy="32" r="5" fill="#f7941d"/><circle cx="18" cy="24" r="2.5" fill="#f7941d"/><circle cx="26" cy="21" r="2.5" fill="#f7941d"/><circle cx="34" cy="24" r="2.5" fill="#f7941d"/></svg>
    <p style="margin-top:12px">With experienced staff in store, we can provide help and information to help you decide on which feed may best suit your horses specific dietary needs.</p></div>
  <div class="btn" style="left:336px;top:2137px;width:89px;height:20px;background:var(--orange-2)">Request quote</div>

  <!-- feedback -->
  <div class="abs" role="img" aria-label="Photo of horses in brown tones behind a dark overlay" style="left:0;top:2198px;width:760px;height:481px;background:linear-gradient(180deg,#5b2a1e,#6b3424 50%,#4e2319)"></div>
  <div class="abs" style="left:0;top:2218px;width:760px;text-align:center;color:#fff;font-size:23px;font-weight:500">FEDDBACK</div>
  <div class="abs rule" style="left:318px;top:2253px;width:82px;height:2px;background:#fff"></div>
  <div class="abs card" style="left:59px;top:2293px"><div class="stars">★★★★★</div><p>lorem ipsum dolor sit amet, consectetur adipiscing elit. nulla sed cum nunc, egestas placerat vulputate id vitae.</p><div class="av"></div><b>DANA WHITFIELD</b><small>CEDAR FALLS</small></div>
  <div class="abs card" style="left:289px;top:2293px"><div class="stars">★★★★★</div><p>lorem ipsum dolor sit amet, consectetur adipiscing elit. nulla sed cum nunc, egestas placerat vulputate id vitae.</p><div class="av"></div><b>DANA WHITFIELD</b><small>CEDAR FALLS</small></div>
  <div class="abs card" style="left:519px;top:2293px"><div class="stars">★★★★★</div><p>lorem ipsum dolor sit amet, consectetur adipiscing elit. nulla sed cum nunc, egestas placerat vulputate id vitae.</p><div class="av"></div><b>DANA WHITFIELD</b><small>CEDAR FALLS</small></div>
  <div class="abs card" style="left:59px;top:2459px"><div class="stars">★★★★★</div><p>lorem ipsum dolor sit amet, consectetur adipiscing elit. nulla sed cum nunc, egestas placerat vulputate id vitae.</p><div class="av"></div><b>DANA WHITFIELD</b><small>CEDAR FALLS</small></div>
  <div class="abs card" style="left:289px;top:2459px"><div class="stars">★★★★★</div><p>lorem ipsum dolor sit amet, consectetur adipiscing elit. nulla sed cum nunc, egestas placerat vulputate id vitae.</p><div class="av"></div><b>DANA WHITFIELD</b><small>CEDAR FALLS</small></div>
  <div class="abs card" style="left:519px;top:2459px"><div class="stars">★★★★★</div><p>lorem ipsum dolor sit amet, consectetur adipiscing elit. nulla sed cum nunc, egestas placerat vulputate id vitae.</p><div class="av"></div><b>DANA WHITFIELD</b><small>CEDAR FALLS</small></div>
  <div class="btn" style="left:336px;top:2618px;width:89px;height:22px;background:var(--orange-2)">View more</div>

  <!-- newsletter -->
  <div class="abs" style="left:71px;top:2679px;width:689px;height:52px;background:var(--orange-2)"></div>
  <div class="abs" style="left:99px;top:2698px;color:#fff;font-size:10px">Subscribe Our Newsletter</div>
  <div class="abs" style="left:255px;top:2690px;width:344px;height:29px;background:#fff;font-size:10px;color:#777;padding:6px 16px">Enter your email</div>
  <div class="abs" style="left:599px;top:2690px;width:100px;height:29px;background:var(--brown);color:#fff;font-size:10px;font-weight:500;display:flex;align-items:center;justify-content:center">Subscribe</div>

  <!-- footer -->
  <div class="abs footer">
    <div class="abs" style="left:54px;top:30px;display:flex;align-items:center;gap:6px;font-size:13px;font-weight:600"><span style="width:10px;height:10px;border-radius:50%;background:var(--orange)"></span>HARVEST HAVEN</div>
    <p class="abs" style="left:44px;top:97px;width:160px;font-size:8px;line-height:13px">Harvest Haven is a locally owned company located in Millbrook, AB. We are dedicated in providing high quality products and services.</p>
    <div class="abs" style="left:52px;top:175px;display:flex;gap:22px"><span style="width:10px;height:10px;border-radius:50%;border:1px solid #fff"></span><span style="width:10px;height:10px;border-radius:50%;border:1px solid #fff"></span><span style="width:10px;height:10px;border-radius:50%;border:1px solid #fff"></span><span style="width:10px;height:10px;border-radius:50%;border:1px solid #fff"></span></div>
    <div class="abs fcol" style="left:230px;top:45px"><h5>PRODUCTS</h5><ul style="line-height:14px"><li>Cats</li><li>Dog</li><li>Rabit</li><li>Birds</li><li>sheep</li><li>pigs</li></ul></div>
    <div class="abs fcol" style="left:380px;top:43px"><h5>CUSTOMER CARE</h5><ul><li>Home</li><li>Our Services</li><li>blog</li><li>About us</li><li>Contact Us</li></ul></div>
    <div class="abs" style="left:544px;top:42px;font-size:14px">Call Now For Services!<div style="color:var(--orange);font-size:15px;margin-top:2px">555-642-0199</div></div>
    <div class="abs" style="left:547px;top:103px;font-size:14px;display:flex;align-items:center;gap:14px"><svg width="16" height="12" viewBox="0 0 16 12" fill="none" stroke="#fff"><rect x=".5" y=".5" width="15" height="11"/><path d="M.5 .5l7.5 6 7.5-6"/></svg>Email Us</div>
    <div class="abs" style="left:549px;top:137px;font-size:14px;display:flex;align-items:center;gap:16px"><svg width="12" height="16" viewBox="0 0 12 16" fill="none" stroke="#fff"><path d="M6 15s5-5.5 5-9A5 5 0 001 6c0 3.5 5 9 5 9z"/><circle cx="6" cy="6" r="2"/></svg>Get Direction</div>
    <div class="abs" style="left:42px;top:210px;width:676px;height:1px;background:rgba(255,255,255,.25)"></div>
    <div class="abs" style="left:0;top:220px;width:760px;text-align:center;font-size:8px">harvest haven © 2021 All Rights Reserved. Terms of Use and Privacy Policy</div>
  </div>

</div>
</body>
</html>
```